Web Design For Manufacturing And Outsourcing Company

Pick up the pieces from our previous developer and help us complete our website.

5 pages - Home,Machining,Sourcing,About Us, and Contact

Attached you will find screen shots of previous direction but we're open to new ideas.

We can provide all text and images needed.

Thanks!

Number of Pages Required

5+ page

```html
<!DOCTYPE html>
<html lang="en">
<head>
<meta charset="utf-8">
<title>Corvane Industries — Machining &amp; Sourcing</title>
<link href="https://fonts.googleapis.com/css2?family=Roboto:wght@400;500;700;900&display=swap" rel="stylesheet">
<style>
:root{
  --orange:#ee5a1c;
  --orange-dark:#c8431a;
  --ink:#222222;
  --text:#3a3a3a;
  --grey-dark:#454547;
  --grey-band:#4a4a4c;
  --light:#ececec;
  --white:#ffffff;
}
*{margin:0;padding:0;box-sizing:border-box}
html,body{width:1200px;height:2848px;overflow:hidden}
body{font-family:"Roboto",Arial,sans-serif;color:var(--text);background:var(--white);position:relative}
.page{position:relative;width:1200px;height:2848px;overflow:hidden;
  background:linear-gradient(180deg,#fff 0,#fff 620px,#f6f6f6 800px,#e4e4e4 1180px,#fff 1181px)}
.layer{position:absolute;left:0;top:0}
.abs{position:absolute}

/* brand */
.brand{position:absolute;display:flex;align-items:center;gap:14px;font-weight:700;letter-spacing:3px;text-transform:uppercase}
.brand-square{width:34px;height:34px;background:var(--orange)}
.brand--hero{left:152px;top:42px;color:var(--white);font-size:16px}
.brand--footer{left:133px;top:2738px;color:var(--grey-dark);font-size:16px}
.brand-mark{position:absolute;width:26px;height:26px;background:var(--orange)}

/* nav */
.main-nav{position:absolute;left:500px;top:62px;display:flex;gap:30px;font-size:16px;font-weight:500;color:var(--white);text-transform:uppercase}

/* hero */
.hero-title{left:171px;top:218px;width:460px;font-size:34px;line-height:45px;font-weight:700;color:var(--white);text-transform:uppercase}
.btn{position:absolute;display:flex;align-items:center;justify-content:center;font-size:16px;font-weight:700;color:var(--white);text-transform:uppercase;background:var(--orange);box-shadow:0 2px 4px rgba(0,0,0,.25)}
.btn--dark{background:var(--grey-dark)}
.slider-arrow{position:absolute;width:52px;height:52px;border-radius:50%;background:rgba(80,80,80,.75);display:flex;align-items:center;justify-content:center}

/* about */
.section-title{position:absolute;left:0;width:1200px;text-align:center;font-weight:700;color:var(--ink);text-transform:uppercase}
.about-title{top:606px;font-size:38px}
.policy-title{top:688px;font-size:23px;color:var(--orange)}
.policy-text{position:absolute;left:256px;top:722px;width:690px;text-align:center;font-size:17px;line-height:28px;color:var(--ink)}
.values-title{top:890px;font-size:24px}
.value{position:absolute;top:958px;width:250px}
.value-icon{position:absolute;left:0;top:2px}
.value-body{margin-left:70px}
.value h3{font-size:17px;font-weight:700;color:var(--orange);text-transform:uppercase;margin-bottom:6px}
.value p{font-size:14.5px;line-height:20px;color:var(--text)}
.value .more{display:block;margin-top:18px;font-size:13px;font-weight:700;color:var(--grey-dark);text-transform:uppercase}

/* sourcing */
.sourcing-title{left:161px;top:1342px;font-size:33px;font-weight:700;color:var(--white);text-transform:uppercase}
.sourcing-text{left:161px;top:1394px;width:450px;font-size:16px;line-height:27px;color:var(--white)}
.feature-card{position:absolute;width:179px;height:174px;background:var(--white);box-shadow:0 3px 8px rgba(0,0,0,.3);text-align:center;padding-top:12px}
.feature-card h4{font-size:19px;font-weight:700;color:var(--ink);text-transform:uppercase;margin-top:6px}
.feature-card p{font-size:13.5px;line-height:17px;color:var(--text);margin:4px auto 0;width:120px}

/* machining */
.machining-title{left:608px;top:1852px;font-size:36px;font-weight:700;color:var(--ink);text-transform:uppercase}
.machining-text{left:608px;top:1913px;width:450px;font-size:17px;line-height:27px;color:var(--ink)}

/* contact */
.cta-title{top:2398px;font-size:31px;line-height:45px;font-weight:400;color:var(--white)}

/* footer */
.footer-nav{position:absolute;left:399px;top:2749px;display:flex;gap:18px;font-size:15px;font-weight:700;color:var(--ink);text-transform:uppercase}
.copyright{position:absolute;left:399px;top:2780px;font-size:12.5px;font-weight:500;color:var(--text)}
.social{position:absolute;top:2743px;width:30px;height:30px;border-radius:50%}
</style>
</head>
<body>
<div class="page">

  <!-- bands and curves -->
  <svg class="layer" width="1200" height="2848" viewBox="0 0 1200 2848" aria-hidden="true">
    <defs>
      <linearGradient id="orangeBand" x1="0" y1="0" x2="1" y2="1">
        <stop offset="0" stop-color="#f26a23"/>
        <stop offset="0.5" stop-color="#e04f18"/>
        <stop offset="1" stop-color="#f47a30"/>
      </linearGradient>
      <linearGradient id="darkBand" x1="0" y1="0" x2="1" y2="0">
        <stop offset="0" stop-color="#5a5a5c"/>
        <stop offset="0.5" stop-color="#2e2e30"/>
        <stop offset="1" stop-color="#4c4c4e"/>
      </linearGradient>
    </defs>
    <path d="M0 1300 C300 1200 700 1172 1200 1172 V1200 C700 1198 300 1232 0 1322 Z" fill="var(--grey-band)"/>
    <path d="M560 1768 C880 1740 1100 1680 1200 1630 V1700 C1100 1740 900 1764 760 1768 Z" fill="var(--grey-band)"/>
    <path d="M0 2214 C420 2196 900 2212 1200 2262 V2292 C900 2236 420 2222 0 2232 Z" fill="var(--orange)"/>
    <path d="M0 2600 C400 2650 900 2658 1200 2620 V2650 C900 2686 400 2676 0 2626 Z" fill="var(--orange)"/>
  </svg>

  <!-- hero photo -->
  <svg class="layer" width="1200" height="640" viewBox="0 0 1200 640" role="img" aria-label="Photo of a CNC lathe machining a polished steel shaft">
    <defs>
      <linearGradient id="heroMetal" x1="0" y1="0" x2="1" y2="1">
        <stop offset="0" stop-color="#d8d8d8"/>
        <stop offset="0.5" stop-color="#bcbcbc"/>
        <stop offset="1" stop-color="#eeeeee"/>
      </linearGradient>
      <linearGradient id="heroTint" x1="0" y1="0" x2="1" y2="1">
        <stop offset="0" stop-color="#7a4a34"/>
        <stop offset="0.6" stop-color="#9a5436"/>
        <stop offset="1" stop-color="#6b4030"/>
      </linearGradient>
    </defs>
    <path d="M0 0 H1200 V540 C900 548 600 590 0 630 Z" fill="url(#heroMetal)"/>
    <path d="M0 0 H805 C775 270 520 520 0 575 Z" fill="url(#heroTint)"/>
    <path d="M805 0 C775 270 520 520 0 575 L0 562 C510 508 760 262 792 0 Z" fill="var(--orange)"/>
  </svg>

  <div class="brand brand--hero"><span class="brand-square"></span>Corvane Industries</div>
  <nav class="main-nav"><span>Home</span><span>Machining Capabilities</span><span>Sourcing</span><span>Contact Us</span></nav>

  <h1 class="abs hero-title">A single point of contact for all your procurement needs</h1>
  <div class="btn" style="left:171px;top:370px;width:163px;height:46px">Read More</div>
  <div class="slider-arrow" style="left:78px;top:287px"><svg width="18" height="18" viewBox="0 0 18 18"><path d="M12 2 L5 9 L12 16" fill="none" stroke="#fff" stroke-width="2.5"/></svg></div>
  <div class="slider-arrow" style="left:1028px;top:287px"><svg width="18" height="18" viewBox="0 0 18 18"><path d="M6 2 L13 9 L6 16" fill="none" stroke="#fff" stroke-width="2.5"/></svg></div>

  <!-- about -->
  <span class="brand-mark" style="left:587px;top:548px"></span>
  <h2 class="section-title about-title">About Us</h2>
  <h3 class="section-title policy-title">Quality Policy</h3>
  <p class="policy-text">We are committed to consistently exceeding customer expectations by providing products, services and sourcing solutions of the highest standard of quality. With our streamlined processes our method is efficient, provides value and ensures on time delivery. Our success isbased on continuously improving the efficiencies and effectiveness of our products</p>

  <h3 class="section-title values-title">Core Values</h3>

  <div class="value" style="left:190px">
    <svg class="value-icon" width="56" height="52" viewBox="0 0 56 52" fill="none" stroke="var(--orange)" stroke-width="2.2">
      <circle cx="16" cy="12" r="7"/><circle cx="40" cy="12" r="7"/><circle cx="28" cy="26" r="7"/>
      <path d="M4 34 a12 10 0 0 1 20 -6"/><path d="M52 34 a12 10 0 0 0 -20 -6"/><path d="M14 50 a14 12 0 0 1 28 0"/>
    </svg>
    <div class="value-body">
      <h3>Teamwork</h3>
      <p>We are one company, one team. We understand when we work together we work smarter and not harder.</p>
      <span class="more">Read More</span>
    </div>
  </div>

  <div class="value" style="left:465px;top:953px">
    <svg class="value-icon" width="60" height="52" viewBox="0 0 60 52" fill="none" stroke="var(--orange)" stroke-width="2.2">
      <path d="M30 48 C10 34 4 24 4 16 a12 12 0 0 1 26 -4 a12 12 0 0 1 26 4 c0 8 -6 18 -26 32 Z"/>
      <path d="M16 26 L26 20 L36 28 M24 34 L34 26"/>
    </svg>
    <div class="value-body">
      <h3>Respect</h3>
      <p>We are one company, one team. We understand when we work together we work smarter and not harder.</p>
      <span class="more">Read More</span>
    </div>
  </div>

  <div class="value" style="left:788px;top:953px">
    <svg class="value-icon" width="56" height="62" viewBox="0 0 56 62" fill="none" stroke="var(--orange)" stroke-width="2.2">
      <rect x="10" y="8" width="34" height="28" rx="6"/><path d="M19 8 V30 M28 8 V30 M36 8 V30"/>
      <path d="M16 36 V60 M38 36 V60"/>
    </svg>
    <div class="value-body">
      <h3>Gratitude</h3>
      <p>We appreciate where we have come from and the opportunities we are given to continue our journey.</p>
      <span class="more">Read More</span>
    </div>
  </div>

  <!-- sourcing photo band -->
  <svg class="layer" style="top:1196px" width="1200" height="574" viewBox="0 0 1200 574" role="img" aria-label="Orange-tinted photo of a machined turbine part">
    <path d="M0 126 C300 36 700 2 1200 4 V440 C950 520 650 560 0 574 Z" fill="url(#orangeBand)"/>
  </svg>

  <h2 class="abs sourcing-title">Sourcing</h2>
  <p class="abs sourcing-text">Pellentesque faucibus Ut accumsan ultricies elit Maecenas at justo id velit placerat molestie Donec dictum lectus non odio Cras a ante vitae enim iaculis aliquam Mauris nunc quam venenatis nec euismod sit amet egestas placerat est Pellentesque habitant morbi tristique senectus et netus et malesuada fames ac turpis egestas Cras id elit</p>
  <div class="btn btn--dark" style="left:163px;top:1573px;width:152px;height:48px">Read More</div>

  <div class="feature-card" style="left:638px;top:1254px">
    <svg width="62" height="62" viewBox="0 0 62 62" fill="none" stroke="var(--orange)" stroke-width="2.2"><circle cx="31" cy="31" r="20"/><circle cx="31" cy="31" r="9"/><path d="M31 5 V11 M31 51 V57 M5 31 H11 M51 31 H57 M13 13 L17 17 M45 45 L49 49 M13 49 L17 45 M45 17 L49 13"/></svg>
    <h4>Vetting</h4><p>Donec dictum lectus non odio Cras</p>
  </div>
  <div class="feature-card" style="left:834px;top:1296px">
    <svg width="62" height="62" viewBox="0 0 62 62" fill="none" stroke="var(--orange)" stroke-width="2.2"><circle cx="31" cy="31" r="24"/><circle cx="31" cy="31" r="17"/><path d="M31 19 L34.5 27 L43 27.5 L36.5 33 L38.5 41.5 L31 37 L23.5 41.5 L25.5 33 L19 27.5 L27.5 27 Z"/></svg>
    <h4>Quality</h4><p>Donec dictum lectus non odio Cras</p>
  </div>
  <div class="feature-card" style="left:638px;top:1455px">
    <svg width="62" height="62" viewBox="0 0 62 62" fill="none" stroke="var(--orange)" stroke-width="2.2"><circle cx="31" cy="31" r="24"/><circle cx="31" cy="31" r="16"/><circle cx="31" cy="31" r="8"/><circle cx="31" cy="31" r="2" fill="var(--orange)"/></svg>
    <h4>Process</h4><p>Donec dictum lectus non odio Cras</p>
  </div>
  <div class="feature-card" style="left:838px;top:1497px">
    <svg width="62" height="62" viewBox="0 0 62 62" fill="none" stroke="var(--orange)" stroke-width="2.2"><rect x="8" y="10" width="46" height="34"/><path d="M14 38 L24 28 L32 33 L46 18 M40 18 H46 V24"/><path d="M31 44 V54 M22 54 H40"/></svg>
    <h4>Benefits</h4><p>Donec dictum lectus non odio Cras</p>
  </div>

  <!-- machining -->
  <svg class="layer" width="1200" height="2848" viewBox="0 0 1200 2848" aria-hidden="true">
    <polygon points="354,1720 562,1838 562,2142 354,2262 146,2142 146,1838" fill="var(--white)"/>
  </svg>
  <svg class="layer" style="left:167px;top:1776px" width="374" height="428" viewBox="0 0 374 428" role="img" aria-label="Photo of a milling spindle cutting metal with sparks">
    <defs>
      <radialGradient id="millPhoto" cx="0.55" cy="0.55" r="0.7">
        <stop offset="0" stop-color="#f2a24a"/>
        <stop offset="0.25" stop-color="#4c7fb8"/>
        <stop offset="0.7" stop-color="#1f3f72"/>
        <stop offset="1" stop-color="#0f1f3a"/>
      </radialGradient>
    </defs>
    <polygon points="187,0 374,107 374,321 187,428 0,321 0,107" fill="url(#millPhoto)"/>
  </svg>

  <h2 class="abs machining-title">Machining</h2>
  <p class="abs machining-text">Pellentesque faucibus Ut accumsan ultricies elit Maecenas at justo id velit placerat molestie Donec dictum lectus non odio Cras a ante vitae enim iaculis aliquam Mauris nunc quam venenatis nec euismod sit amet egestas placerat est Pellentesque habitant morbi tristique senec</p>
  <div class="btn" style="left:610px;top:2079px;width:156px;height:49px">Read More</div>

  <!-- contact band -->
  <svg class="layer" style="top:2226px" width="1200" height="420" viewBox="0 0 1200 420" role="img" aria-label="Dark photo of a lathe chuck and tooling">
    <path d="M0 6 C420 -4 900 12 1200 62 V396 C900 430 400 424 0 376 Z" fill="url(#darkBand)"/>
  </svg>
  <span class="brand-mark" style="left:587px;top:2342px"></span>
  <h2 class="section-title cta-title">Contact us today with your machining<br>or sourcing needs!</h2>
  <div class="btn" style="left:506px;top:2508px;width:204px;height:49px">Get In Touch</div>

  <!-- footer -->
  <div class="brand brand--footer"><span class="brand-square"></span>Corvane Industries</div>
  <nav class="footer-nav"><span>Home</span><span>Machining Capabilities</span><span>Sourcing</span><span>Contact Us</span></nav>
  <p class="copyright">© 2019 Company Name &nbsp;All right reserved</p>
  <span class="social" style="left:925px;background:#3b5a9a"></span>
  <span class="social" style="left:963px;background:#4aa0e6"></span>
  <span class="social" style="left:999px;background:#3a5f8a"></span>
  <span class="social" style="left:1035px;background:#1f74b0"></span>

</div>
</body>
</html>
```